Business Card Design Project - 2 sided

We need a business card design for a card having one business on each side (ie. two businesses on one card). Would like a design that incorporates logo, tagline and normal fields (name, position, address, phone).

Would also like an allowance for small font text along the bottom (text to be determined, but less than 50 characters).

NB. Attached logo for Harbor Quill has two variations - either can be used.

www.harborquill-example.com / www.velmaro-example.com

```html
<!DOCTYPE html>
<html lang="en">
<head>
<meta charset="utf-8">
<title>Harbor Quill / Velmaro LLC – Business Card</title>
<link rel="stylesheet" href="https://fonts.googleapis.com/css2?family=Open+Sans:wght@400;600;700&display=swap">
<style>
  :root {
    --backdrop: #eceae6;
    --card-white: #ffffff;
    --navy: #2a2761;
    --navy-text: #3a3478;
    --green: #8cc63f;
    --blue-top: #55addc;
    --blue-bottom: #1c7db5;
    --blue-text: #2a8ac4;
    --ink: #2b2b2b;
    --band-text: #ffffff;
  }
  * { box-sizing: border-box; margin: 0; padding: 0; }
  html, body { width: 1200px; height: 402px; overflow: hidden; }
  body {
    background: var(--backdrop);
    font-family: "Open Sans", Arial, sans-serif;
    position: relative;
  }
  .card {
    position: absolute;
    top: 55px;
    width: 512px;
    height: 291px;
    border-radius: 14px;
    background: var(--card-white);
    overflow: hidden;
    box-shadow: 0 2px 6px rgba(0,0,0,.18);
  }
  .card--harbor { left: 61px; }
  .card--velmaro { left: 626px; }

  .brand {
    position: absolute;
    left: 0; right: 0;
    display: flex;
    align-items: center;
    justify-content: center;
    gap: 12px;
  }
  .brand__dot { border-radius: 50%; flex: none; }
  .brand__name { font-weight: 600; line-height: 1; }

  .card--harbor .brand { top: 52px; }
  .card--harbor .brand__dot { width: 34px; height: 34px; background: var(--green); }
  .card--harbor .brand__name { font-size: 26px; color: var(--navy-text); letter-spacing: 1px; }

  .card--velmaro .brand { top: 40px; }
  .card--velmaro .brand__dot { width: 50px; height: 50px; background: var(--green); }
  .card--velmaro .brand__name { font-size: 40px; color: var(--blue-text); }

  .tagline {
    position: absolute;
    left: 0; right: 0;
    text-align: center;
    color: var(--ink);
  }
  .card--harbor .tagline { top: 111px; font-size: 10px; }
  .card--velmaro .tagline { top: 96px; left: 80px; font-size: 14px; color: #444; letter-spacing: .5px; }

  .fineprint {
    position: absolute;
    top: 142px;
    left: 0; right: 0;
    text-align: center;
    font-size: 9px;
    color: var(--ink);
    letter-spacing: .2px;
  }

  .band {
    position: absolute;
    left: 0; right: 0; bottom: 0;
    height: 131px;
    color: var(--band-text);
  }
  .card--harbor .band { background: var(--navy); }
  .card--velmaro .band { background: linear-gradient(180deg, var(--blue-top), var(--blue-bottom)); }
  .band__pointer {
    position: absolute;
    top: -1px; left: 147px;
    width: 18px; height: 13px;
  }

  .person {
    position: absolute;
    right: 269px;
    top: 36px;
    text-align: right;
    white-space: nowrap;
  }
  .person__name { font-size: 15px; font-weight: 700; }
  .person__title { font-size: 12px; }
  .address {
    position: absolute;
    right: 269px;
    top: 81px;
    text-align: right;
    font-size: 12px;
    line-height: 17px;
    white-space: nowrap;
  }
  .divider {
    position: absolute;
    left: 273px;
    top: 22px;
    width: 1px;
    height: 100px;
    background: rgba(255,255,255,.8);
  }
  .contacts {
    position: absolute;
    left: 306px;
    top: 25px;
    list-style: none;
    font-size: 12px;
    line-height: 17.3px;
  }
  .contacts li { display: flex; align-items: center; gap: 5px; white-space: nowrap; }
  .contacts svg { width: 9px; height: 9px; flex: none; fill: currentColor; }
</style>
</head>
<body>

<svg width="0" height="0" style="position:absolute" aria-hidden="true">
  <defs>
    <symbol id="icon-phone" viewBox="0 0 10 10"><path d="M2 .5 3.6 2.6 2.8 3.6c.6 1.4 2 2.8 3.6 3.6l1-.8L9.5 8 8.3 9.5C4 9.2.8 6 .5 1.7Z"/></symbol>
    <symbol id="icon-mobile" viewBox="0 0 10 10"><path d="M3 0h4a1 1 0 0 1 1 1v8a1 1 0 0 1-1 1H3a1 1 0 0 1-1-1V1a1 1 0 0 1 1-1Zm0 1.5v5.5h4V1.5Z"/></symbol>
    <symbol id="icon-fax" viewBox="0 0 10 10"><path d="M.5 3.5C2 1.8 8 1.8 9.5 3.5L8.6 5 7 4.4V3.6H3v.8L1.4 5ZM2.5 5.5h5L9 9.5H1Z"/></symbol>
    <symbol id="icon-mail" viewBox="0 0 10 10"><path d="M0 4 5 .8 10 4v5.2H0Zm1 .6v.3L5 7.4 9 4.9v-.3L5 7Z"/></symbol>
    <symbol id="icon-web" viewBox="0 0 10 10"><circle cx="5" cy="5" r="4.6"/><path d="M.6 5h8.8" stroke="#fff" stroke-width=".8"/></symbol>
  </defs>
</svg>

<section class="card card--harbor">
  <div class="brand">
    <span class="brand__dot"></span>
    <span class="brand__name">Harbor Quill</span>
  </div>
  <p class="tagline">Website Translation and Localisation Specialist...</p>
  <p class="fineprint">xxxxxxxxxxxxxxxxxxxxxxxxxx xxxxxxxxxxxxxxxxxxxxxxxxxx</p>
  <div class="band">
    <svg class="band__pointer" viewBox="0 0 18 13"><path d="M0 0h18L9 13Z" fill="#fff"/></svg>
    <p class="person"><span class="person__name">Your Name</span> <span class="person__title">/ Title</span></p>
    <p class="address">Complex name, Street name<br>City, State, zip code</p>
    <span class="divider"></span>
    <ul class="contacts">
      <li><svg><use href="#icon-phone"/></svg>123-456-7890</li>
      <li><svg><use href="#icon-mobile"/></svg>123-456-7890</li>
      <li><svg><use href="#icon-fax"/></svg>123-456-7890</li>
      <li><svg><use href="#icon-mail"/></svg>name@website.com</li>
      <li><svg><use href="#icon-web"/></svg>www.website.com</li>
    </ul>
  </div>
</section>

<section class="card card--velmaro">
  <div class="brand">
    <span class="brand__dot"></span>
    <span class="brand__name">Velmaro LLC</span>
  </div>
  <p class="tagline">Professional SEO Services</p>
  <p class="fineprint">xxxxxxxxxxxxxxxxxxxxxxxxxx xxxxxxxxxxxxxxxxxxxxxxxxxx</p>
  <div class="band">
    <svg class="band__pointer" viewBox="0 0 18 13"><path d="M0 0h18L9 13Z" fill="#fff"/></svg>
    <p class="person"><span class="person__name">Your Name</span> <span class="person__title">/ Title</span></p>
    <p class="address">Complex name, Street name<br>City, State, zip code</p>
    <span class="divider"></span>
    <ul class="contacts">
      <li><svg><use href="#icon-phone"/></svg>123-456-7890</li>
      <li><svg><use href="#icon-mobile"/></svg>123-456-7890</li>
      <li><svg><use href="#icon-fax"/></svg>123-456-7890</li>
      <li><svg><use href="#icon-mail"/></svg>name@website.com</li>
      <li><svg><use href="#icon-web"/></svg>www.website.com</li>
    </ul>
  </div>
</section>

</body>
</html>
```